Harborview Estates Business Card for Apartment Buildings

Create business cards for resident managers who run apartment buildings. The audience is the public who are searching for apartment rentals, and current residents who live at the apartment building. Key design element will be incorporating the company logo, however, the logo cannot dominate. The building name and manager name are more important than the logo. Current business card design leaves little room for copy, so we may need to reduce the size on the current card to allow for more space for copy.

Target Market(s)

Adults 18-65 years of age, who are looking for an apartment rental, plus current residents who live at our apartment buildings.

Industry/Entity Type

Property Management

Contact Information for Business Card

A major design element will be use of the company logo. Important property and manager contact information must be part of the design. The size of the logo will need to be reduced to make room for building and manager contact copy.

Font styles to use
Sans Serif

Colors
3176b5
000000
959595
ffffff

Requirements
Must have
• 1) Incorporate the company logo.
• 2) Use the company colors (dark blue, black/grey, over white).
• 3) FEATURE THE BUILDING NAME
• 4) FEATURE THE MANAGER NAME
• 5) The company name is less important than BUILDING and MANAGER
• 6) Manager contact information
• **SEE ATTACHED CREATIVE BRIEF**
Nice to have
• 1) Back of card logo watermark
• 2) Ability to write notes on back of carfd
Should not have
• Avoid letting the company logo dominate the card, the building name and manager are more important than the company logo.

```html
<!DOCTYPE html>
<html lang="en">
<head>
<meta charset="utf-8">
<title>Harborview Estates – Resident Manager Business Card</title>
<link rel="stylesheet" href="https://fonts.googleapis.com/css2?family=Catamaran:wght@400;600;700&display=swap">
<style>
  :root {
    --brand-blue: #3176b5;
    --ink: #000000;
    --grey: #959595;
    --dark-grey: #4a4a4a;
    --text-grey: #5c5c5c;
    --paper: #ffffff;
    --backdrop: #2b2b2b;
  }
  * { box-sizing: border-box; margin: 0; padding: 0; }
  html, body {
    width: 1200px; height: 895px; overflow: hidden;
    background: var(--backdrop);
    font-family: "Catamaran", sans-serif;
  }
  .canvas { position: relative; width: 1200px; height: 895px; }
  .card {
    position: absolute; left: 350px; width: 490px; height: 278px;
    background: var(--paper); overflow: hidden;
  }
  .card--front { top: 160px; }
  .card--back { top: 468px; }

  /* Front */
  .brand-lockup {
    position: absolute; left: 30px; top: 108px; width: 240px;
  }
  .brand-name {
    display: flex; align-items: center; gap: 8px;
    font-weight: 700; font-size: 25px; line-height: 1;
    color: var(--brand-blue); letter-spacing: 0.5px; text-transform: uppercase;
  }
  .brand-dot { width: 12px; height: 12px; background: var(--brand-blue); flex: none; }
  .building-name {
    margin-top: 6px; padding-left: 20px;
    font-weight: 700; font-size: 10.5px; letter-spacing: 0.6px;
    color: var(--dark-grey); text-transform: uppercase;
  }
  .divider {
    position: absolute; left: 288px; top: 66px; width: 1.5px; height: 143px;
    background: var(--grey);
  }
  .contact { position: absolute; left: 310px; top: 62px; }
  .manager-name {
    font-weight: 700; font-size: 17px; color: var(--brand-blue); line-height: 1.2;
  }
  .manager-role, .address, .contact-line {
    font-size: 10.5px; color: var(--text-grey); line-height: 1.6;
  }
  .manager-role { margin-bottom: 4px; }
  .address { margin-bottom: 4px; }
  .contact-line { display: flex; align-items: center; gap: 6px; }
  .contact-line svg { width: 9px; height: 9px; fill: var(--brand-blue); flex: none; }
  .card-band { position: absolute; left: 0; bottom: 0; width: 490px; height: 8px; }

  /* Back */
  .back-mark {
    position: absolute; left: 0; right: 0; top: 118px;
    text-align: center;
    font-weight: 700; font-size: 25px; color: var(--brand-blue);
    letter-spacing: 0.5px; text-transform: uppercase;
  }
  .website {
    position: absolute; left: 0; right: 0; top: 242px;
    text-align: center; font-size: 11px; letter-spacing: 1px;
    color: var(--brand-blue); font-weight: 600;
  }
</style>
</head>
<body>
<main class="canvas">
  <section class="card card--front" aria-label="Business card front">
    <div class="brand-lockup">
      <div class="brand-name"><span class="brand-dot"></span>Harborview Estates</div>
      <div class="building-name">Seacrest Court Apartments</div>
    </div>
    <div class="divider"></div>
    <div class="contact">
      <h1 class="manager-name">Marisol Delgado</h1>
      <p class="manager-role">Resident Manager</p>
      <p class="address">2480 Cedar Lane Street<br>Bayview, CA 90210</p>
      <p class="contact-line">
        <svg viewBox="0 0 10 10"><path d="M2 0.5l2 2-1 1.2c.6 1.3 1.6 2.3 2.8 2.8l1.2-1 2 2-1.2 1.8C4.5 9.3.7 5.5.3 1.7z"/></svg>555-240-1180
      </p>
      <p class="contact-line">
        <svg viewBox="0 0 10 10"><rect x="2.5" y="0.5" width="5" height="2.5"/><rect x="0.5" y="3.5" width="9" height="4" rx="0.6"/><rect x="2.5" y="6.5" width="5" height="3"/></svg>555-240-1195
      </p>
      <p class="contact-line">
        <svg viewBox="0 0 10 10"><path d="M2.5 0h5a.7.7 0 0 1 .7.7v8.6a.7.7 0 0 1-.7.7h-5a.7.7 0 0 1-.7-.7V.7A.7.7 0 0 1 2.5 0zm.6 1.2v6.6h3.8V1.2z"/></svg>555-318-4420
      </p>
      <p class="contact-line">
        <svg viewBox="0 0 10 10"><path d="M.5 2h9v6h-9zm1 1v.3L5 5.6l3.5-2.3V3zm0 1.5V7h7V4.5L5 6.8z"/></svg>marisol@harborviewest.com
      </p>
    </div>
    <svg class="card-band" viewBox="0 0 490 8" preserveAspectRatio="none" aria-hidden="true">
      <polygon points="0,0 292,0 284,8 0,8" fill="var(--brand-blue)"/>
      <polygon points="296,0 490,0 490,8 288,8" fill="var(--dark-grey)"/>
    </svg>
  </section>

  <section class="card card--back" aria-label="Business card back">
    <div class="back-mark">Harborview Estates</div>
    <p class="website">www.harborviewestates.us</p>
  </section>
</main>
</body>
</html>
```